Need logo and design for business card "FernGlen Plumbing Services".

Needing a design for plumbing company 'FernGlen Plumbing Services', a company based on the surfcoast.
Would like the colour black and blue incorporated. We offer free quotes and reliable friendly service, but don't want this writing on front of card.

I do not have a logo so wanting ideas. Any logo ideas on it would be great.

Target Market(s)

People wanting a Plumber

Industry/Entity Type

Business

Requirements
Must have
• Domestic Plumbing
• Commercial Plumbing
• Roofing
• Gasfitting
Nice to have
• Maybe some sort of plumbing picture on it, spanner, toilet, tap with water etc. Just relating to plumbing.
• FernGlen is on word also with the capital A in it.

```html
<!DOCTYPE html>
<html lang="en">
<head>
<meta charset="utf-8">
<title>FernGlen Plumbing Services – Business Card</title>
<link rel="stylesheet" href="https://fonts.googleapis.com/css2?family=Quicksand:wght@500;700&display=swap">
<style>
  :root {
    --page-bg: #e9e6e1;
    --card-dark: #050505;
    --card-mid: #2a2a2c;
    --ink-light: #f2f2f2;
    --ink-soft: #c9c9c9;
    --brand-blue: #8db3d8;
    --rule: #e6e6e6;
  }
  * { box-sizing: border-box; margin: 0; padding: 0; }
  html, body {
    width: 1200px; height: 1000px; overflow: hidden;
    background: var(--page-bg);
    font-family: "Quicksand", "Helvetica Neue", Arial, sans-serif;
  }
  .canvas { position: relative; width: 1200px; height: 1000px; }

  .card {
    position: absolute;
    width: 600px; height: 343px;
    border-radius: 4px;
    background: linear-gradient(135deg, var(--card-dark) 0%, var(--card-mid) 55%, var(--card-dark) 100%);
    box-shadow: 0 14px 30px rgba(0,0,0,.28);
    color: var(--ink-light);
    overflow: hidden;
  }
  .card--front { left: 60px; top: 70px; }
  .card--back  { left: 540px; top: 585px; }

  /* wordmark */
  .wordmark { position: absolute; display: flex; align-items: flex-start; gap: 10px; }
  .wordmark__dot {
    width: 14px; height: 14px; border-radius: 50%;
    background: var(--brand-blue); margin-top: 16px;
  }
  .wordmark__text { color: var(--brand-blue); font-weight: 700; line-height: 1; }
  .wordmark__name { display: block; }
  .wordmark__sub { display: block; text-transform: uppercase; letter-spacing: .5px; }

  .card--front .wordmark { left: 42px; top: 40px; }
  .card--front .wordmark__name { font-size: 50px; }
  .card--front .wordmark__sub { font-size: 19px; margin-top: 12px; padding-top: 8px; border-top: 3px solid var(--rule); }

  .services {
    position: absolute; left: 150px; top: 170px;
    list-style: none; text-align: center;
    font-size: 25px; font-weight: 500; line-height: 1.28;
    color: var(--ink-light);
  }

  /* back */
  .holder { position: absolute; left: 40px; top: 34px; font-size: 36px; font-weight: 500; }
  .divider {
    position: absolute; left: 40px; right: 40px; top: 92px;
    height: 3px; background: var(--rule);
  }
  .card--back .wordmark { right: 40px; top: 28px; }
  .card--back .wordmark__dot { width: 10px; height: 10px; margin-top: 10px; }
  .card--back .wordmark__name { font-size: 30px; }
  .card--back .wordmark__sub { font-size: 12px; margin-top: 4px; }

  .contacts {
    position: absolute; left: 40px; top: 118px;
    list-style: none; font-size: 15px; font-weight: 500; color: var(--ink-soft);
  }
  .contacts li { display: flex; align-items: center; gap: 10px; height: 26px; }
  .contacts svg { width: 16px; height: 16px; fill: var(--ink-soft); }
  .address {
    position: absolute; right: 40px; bottom: 30px;
    display: flex; align-items: center; gap: 10px;
    font-size: 15px; font-weight: 500; color: var(--ink-soft);
  }
  .address svg { width: 14px; height: 18px; fill: var(--ink-soft); }
</style>
</head>
<body>
<main class="canvas">

  <section class="card card--front" aria-label="Card front">
    <div class="wordmark">
      <span class="wordmark__dot"></span>
      <span class="wordmark__text">
        <span class="wordmark__name">FernGlen</span>
        <span class="wordmark__sub">Plumbing Services</span>
      </span>
    </div>
    <ul class="services">
      <li>Domestic Plumbing</li>
      <li>Commercial Plumbing</li>
      <li>Roofing</li>
      <li>Gasfitting</li>
    </ul>
  </section>

  <section class="card card--back" aria-label="Card back">
    <h1 class="holder">John Doe</h1>
    <div class="wordmark">
      <span class="wordmark__dot"></span>
      <span class="wordmark__text">
        <span class="wordmark__name">FernGlen</span>
        <span class="wordmark__sub">Plumbing Services</span>
      </span>
    </div>
    <div class="divider"></div>
    <ul class="contacts">
      <li>
        <svg viewBox="0 0 24 24" aria-hidden="true"><path d="M6.6 10.8a15 15 0 0 0 6.6 6.6l2.2-2.2a1 1 0 0 1 1-.25 11.4 11.4 0 0 0 3.6.6 1 1 0 0 1 1 1V20a1 1 0 0 1-1 1A17 17 0 0 1 3 4a1 1 0 0 1 1-1h3.5a1 1 0 0 1 1 1c0 1.25.2 2.45.6 3.6a1 1 0 0 1-.25 1z"/></svg>
        123 456 7890
      </li>
      <li>
        <svg viewBox="0 0 24 24" aria-hidden="true"><path d="M7 3h10v5H7zM4 9h16a1 1 0 0 1 1 1v7h-4v4H7v-4H3v-7a1 1 0 0 1 1-1zm5 7v3h6v-3z"/></svg>
        123 456 7890
      </li>
      <li>
        <svg viewBox="0 0 24 24" aria-hidden="true"><path d="M3 5h18v14H3zm2 2v.5l7 5 7-5V7l-7 5z"/></svg>
        yourname@domaine.com
      </li>
      <li style="padding-left:26px">www.domaine.com</li>
    </ul>
    <div class="address">
      <svg viewBox="0 0 14 18" aria-hidden="true"><path d="M7 0a7 7 0 0 0-7 7c0 5 7 11 7 11s7-6 7-11a7 7 0 0 0-7-7zm0 9.5A2.5 2.5 0 1 1 7 4.5a2.5 2.5 0 0 1 0 5z"/></svg>
      Your Adresse here
    </div>
  </section>

</main>
</body>
</html>
```